Design logo, business cards, and web page for new web and bi development consulting company

I've started a Web and Business Intelligence development consulting company. We develop on Quordex's stack, Visual Sudio and SQL Server. We develop responsive web sites and business intelligence platforms. I plan on focusing on small to medium sized business as my client base. I need a logo, business cards, and a one page web site. We will do more with the web site with you in the next six months if the business survives. The name of the company is Corvalo Integration Solutions, Corvalo for short.

Target Market(s)

small to medium sized businesses

Industry/Entity Type

Business

Contact Information for Business Card

logo
name
title
email
phone

Logo Text

Corvalo Integration Solutions - web and data solutions

Coding

Coded - Design and coding required

Number of Pages Required

1 page

Font styles to use
Sans Serif

Colors
0355a3
0092cd
00a88f
6b449b

Requirements
Nice to have
• web and data solutions

```html
<!DOCTYPE html>
<html lang="en">
<head>
<meta charset="utf-8">
<title>Corvalo Integration Solutions</title>
<link rel="stylesheet" href="https://fonts.googleapis.com/css2?family=Roboto:wght@300;400;500;700&display=swap">
<style>
:root{
  --teal:#1ca78b;
  --teal-dark:#12826c;
  --teal-soft:#5cc2aa;
  --ink:#333;
  --muted:#8a8a8a;
  --line:#d9d9d9;
  --paper:#ffffff;
  --mist:#efefef;
  --track:#dcdcdc;
}
*{box-sizing:border-box;margin:0;padding:0}
html,body{width:1200px;height:5217px;overflow:hidden}
body{position:relative;font-family:"Roboto",Arial,sans-serif;color:var(--ink);background:var(--paper)}
.abs{position:absolute}
.section{position:absolute;left:0;width:1200px}
.title{position:absolute;left:0;width:1200px;text-align:center;font-size:34px;font-weight:300;color:var(--ink)}
.title em{font-style:normal;color:var(--teal)}
.btn{position:absolute;background:var(--teal);color:#fff;font-size:14px;display:flex;align-items:center;justify-content:center}

/* hero */
.hero{top:0;height:654px;background:
  radial-gradient(ellipse 380px 260px at 860px 250px,rgba(20,90,78,.55),transparent 70%),
  radial-gradient(ellipse 300px 220px at 620px 300px,rgba(14,110,92,.45),transparent 70%),
  radial-gradient(circle 90px at 1060px 320px,rgba(10,70,60,.5),transparent 70%),
  radial-gradient(circle 120px at 110px 250px,rgba(255,255,255,.12),transparent 70%),
  linear-gradient(160deg,#3fb89e 0%,#2aa28a 40%,#5cbfa8 75%,#8fd3c0 100%)}
.hero-nav{left:255px;top:20px}
.hero-brand{left:410px;top:280px;color:#fff;font-size:50px;font-weight:300}
.hero-sub{left:410px;top:350px;color:#fff;font-size:27px;font-weight:700}
.hero-text{left:410px;top:396px;width:560px;color:#e9f7f3;font-size:14px;line-height:21px}
.hero-down{left:975px;top:548px}

/* main nav */
.mainbar{top:654px;height:87px;background:#f2f2f2}
.logo{left:245px;top:10px;color:var(--teal);font-size:30px;font-weight:500;line-height:30px}
.logo small{display:block;font-size:16px;line-height:22px;font-weight:500}
.menu{left:497px;top:0;height:87px;display:flex;list-style:none}
.menu li{height:87px;padding:0 17px;display:flex;align-items:center;font-size:12px;color:#555}
.menu li.active{background:var(--teal);color:#fff}

/* about */
.about{top:741px;height:494px}
.about-slider{left:257px;top:104px;width:390px;height:292px;background:
  radial-gradient(circle 70px at 140px 150px,#2b2b2b 0%,#5a5a58 55%,transparent 75%),
  linear-gradient(180deg,transparent 60%,#8a6a4c 62%,#b48f6a 100%),
  linear-gradient(120deg,#e9e6e0 0%,#cfc8bc 45%,#9a958c 100%)}
.about-slider .edge{position:absolute;top:0;width:48px;height:292px;background:var(--teal);opacity:.92}
.about-text{left:668px;top:100px;width:290px;font-size:12px;line-height:19px;color:var(--muted)}

/* banners */
.photo-band{background:
  linear-gradient(180deg,rgba(160,175,170,.7) 0%,rgba(160,175,170,0) 30%),
  radial-gradient(ellipse 500px 120px at 300px 60%,rgba(255,255,255,.18),transparent 70%),
  linear-gradient(180deg,#8fa3a0 0%,#4f9f8c 45%,#2e9a82 70%,#1f7f6b 100%)}
.ceo{top:1235px;height:372px}
.ceo .title{color:#fff;top:88px;font-size:32px}
.ceo-quote{left:240px;top:162px;width:720px;text-align:center;color:#eaf6f2;font-size:13px;font-style:italic;line-height:22px}
.qmark{color:#fff;font-size:40px;font-weight:700;position:absolute}

/* team */
.team{top:1607px;height:636px}
.arrows{left:548px;top:148px}
.member{position:absolute;top:278px;width:200px;text-align:center}
.portrait{width:160px;height:160px;border-radius:50%;border:5px solid var(--teal);margin:0 auto}
.portrait.p1{background:radial-gradient(circle 45px at 50% 48%,#e8c8b2,transparent 75%),linear-gradient(160deg,#b98a62,#e6ddd4 60%,#f4f1ee)}
.portrait.p2{background:radial-gradient(circle 42px at 50% 46%,#d8b39c,transparent 75%),linear-gradient(180deg,#3a3634 0%,#5b5450 55%,#1d1b1a 100%)}
.portrait.p3{background:radial-gradient(circle 42px at 50% 46%,#efcdb8,transparent 75%),linear-gradient(170deg,#4a3226,#cbb9ad 60%,#e9e4df)}
.member h4{margin-top:44px;font-size:14px;font-weight:400;color:#555}
.member p{margin-top:8px;font-size:11px;color:var(--muted)}
.dots{display:flex;gap:10px;justify-content:center;margin-top:22px}

/* skills */
.skills{top:2243px;height:446px;background:var(--mist)}
.skill{position:absolute;width:264px}
.skill .lab{display:flex;justify-content:space-between;font-size:11px}
.skill .lab b{font-weight:700}
.skill .lab span{color:var(--muted)}
.bar{margin-top:12px;height:9px;background:var(--track)}
.bar i{display:block;height:9px;background:var(--teal)}

/* services banner */
.services{top:2689px;height:379px}
.services-text{left:0;width:1200px;top:250px;text-align:center;color:#fff;font-size:30px;line-height:42px;font-weight:300}

/* stats */
.stats{top:3068px;height:480px;background:var(--mist)}
.stat{position:absolute;top:50px;width:160px;text-align:center}
.stat b{display:block;font-size:40px;font-weight:300}
.stat span{display:block;font-size:10px;color:var(--muted);margin-top:8px}
.stat-rule{position:absolute;top:60px;width:1px;height:56px;background:var(--line)}
.avatar{left:565px;top:210px;width:70px;height:70px;border-radius:50%;background:radial-gradient(circle 16px at 50% 38%,#e3c0a8,transparent 75%),linear-gradient(180deg,#f2f2f2 0%,#d8d4d0 45%,#1e1e1e 70%,#2b2b2b 100%)}
.quote{left:300px;top:296px;width:600px;text-align:center;font-size:19px;line-height:28px;color:#444}
.cite{left:0;width:1200px;top:370px;text-align:center;font-size:11px;color:#666}
.pager{left:558px;top:440px;display:flex;gap:8px}
.pager i{width:8px;height:8px;border-radius:50%;background:#c8c8c8}
.pager i.on{background:#888}

/* portfolio */
.portfolio{top:3548px;height:852px}
.filters{left:0;width:1200px;top:130px;display:flex;justify-content:center;gap:8px}
.filters span{border:1px solid #bbb;font-size:10px;padding:4px 14px;color:#666}
.filters span.on{background:var(--teal);border-color:var(--teal);color:#fff}
.work{position:absolute;width:216px}
.work .shot{height:216px}
.work h5{margin-top:12px;text-align:center;font-size:14px;font-weight:400}
.work p{text-align:center;font-size:10px;color:var(--muted);margin-top:3px}

/* contact */
.contact{top:4400px;height:817px;background:
  radial-gradient(ellipse 60px 80px at 760px 160px,rgba(230,160,110,.75),transparent 75%),
  radial-gradient(ellipse 160px 260px at 120px 520px,rgba(60,80,80,.45),transparent 75%),
  linear-gradient(180deg,transparent 70%,#8c8a80 78%,#5a5850 100%),
  linear-gradient(180deg,#b9d3d6 0%,#9fc6c4 40%,#7aa5a0 70%,#5f7c7a 100%)}
.panel{left:219px;top:38px;width:870px;height:710px;background:rgba(255,255,255,.55)}
.field{position:absolute;left:52px;width:320px;height:44px;border:1px solid #bfc7c6;background:rgba(255,255,255,.5);font-size:12px;color:#555;padding:14px 12px}
.contact-info{left:414px;width:350px;font-size:13px;line-height:20px;color:#444}
.contact-info b{font-weight:700}
.social{left:414px;top:463px;display:flex;gap:16px}
.footer{left:0;top:748px;width:1200px;height:69px;color:#fff;font-size:11px}
</style>
</head>
<body>

<!-- Hero -->
<header class="section hero" role="img" aria-label="Teal photo montage of a running zebra dissolving into fragments with a small tree on a floating book">
  <svg class="abs hero-nav" width="140" height="620" viewBox="0 0 140 620" fill="none" stroke="#fff" stroke-width="2">
    <line x1="70" y1="120" x2="70" y2="130"/><line x1="70" y1="242" x2="70" y2="252"/><line x1="70" y1="364" x2="70" y2="374"/><line x1="70" y1="486" x2="70" y2="496"/>
    <polygon points="70,8 123,37 123,93 70,122 17,93 17,37" fill="rgba(255,255,255,.08)"/>
    <polygon points="70,130 123,159 123,215 70,244 17,215 17,159" fill="rgba(255,255,255,.08)"/>
    <polygon points="70,252 123,281 123,337 70,366 17,337 17,281" fill="rgba(255,255,255,.08)"/>
    <polygon points="70,374 123,403 123,459 70,488 17,459 17,403" fill="rgba(255,255,255,.08)"/>
    <polygon points="70,496 123,525 123,581 70,610 17,581 17,525" fill="rgba(255,255,255,.08)"/>
    <circle cx="70" cy="55" r="9"/><circle cx="70" cy="55" r="3"/>
    <circle cx="70" cy="170" r="8"/><path d="M56 192c2-10 26-10 28 0"/>
    <path d="M54 288h32v18h-20l-8 7v-7h-4z"/>
    <path d="M58 430l20-20 6 6-20 20h-6z"/>
    <path d="M52 552l36-14-12 32-6-12z"/>
    <g fill="#fff" stroke="none" font-family="Roboto,Arial,sans-serif" font-size="10" text-anchor="middle">
      <text x="70" y="92">About</text><text x="70" y="214">Team</text><text x="70" y="336">Services</text><text x="70" y="458">Blog</text><text x="70" y="580">Contact</text>
    </g>
  </svg>
  <div class="abs hero-brand">Corvalo</div>
  <div class="abs hero-sub">Fusce rutrum pretium lorem semper nulla.</div>
  <p class="abs hero-text">Vestibulum ornare cursus nisl, fermentum tincidunt lorem pretium et. Maecenas vitae dum ligula nam fermentum fringilla.</p>
  <svg class="abs hero-down" width="70" height="74" viewBox="0 0 70 74" fill="none" stroke="#fff" stroke-width="2">
    <polygon points="35,3 66,20 66,54 35,71 4,54 4,20"/><path d="M26 33l9 9 9-9"/>
  </svg>
</header>

<!-- Main navigation -->
<nav class="section mainbar">
  <div class="abs logo">Corvalo<small>Integration Solutions</small></div>
  <ul class="abs menu">
    <li class="active">HOME</li><li>ABOUT</li><li>TEAM</li><li>SERVICES</li><li>PORTFOLIO</li><li>BLOG</li><li>CONTACT</li>
  </ul>
</nav>

<!-- About -->
<section class="section about">
  <h2 class="title" style="top:48px">About <em>us</em></h2>
  <div class="abs about-slider" role="img" aria-label="Desk photo with a speaker beside a laptop in a bright office">
    <div class="edge" style="left:0"></div><div class="edge" style="right:0"></div>
    <svg class="abs" style="left:16px;top:136px" width="14" height="20" fill="none" stroke="#fff" stroke-width="3"><path d="M11 2l-8 8 8 8"/></svg>
    <svg class="abs" style="right:16px;top:136px" width="14" height="20" fill="none" stroke="#fff" stroke-width="3"><path d="M3 2l8 8-8 8"/></svg>
  </div>
  <p class="abs about-text">Aliquam tellus neque, tincidunt sit amet porta at, consequat at enim. Ut et purus nisi. Nullam tincidunt lorem sit amet nibh suscipit, eget feugiat nisl luctus. Maecenas interdum dignissim lorem quis auctor. Donec sit amet nibh eu risus luctus scelerisque. Pellentesque quis enim at mi vehicula placerat. Aenean nec tellus vel nunc pretium tempus at ac lacus. Curabitur vel porta est, sed malesuada augue. Quisque tincidunt mauris vitae eros elementum, in fermentum odio porttitor. Sed at lorem eget erat imperdiet dapibus ac eu nisl.</p>
  <div class="btn" style="left:814px;top:351px;width:136px;height:46px">Learn more</div>
</section>

<!-- CEO message -->
<section class="section ceo photo-band" role="img" aria-label="Blurred teal-toned photo of a shoreline under a grey sky">
  <h2 class="title">CEO MASSAGE</h2>
  <span class="qmark" style="left:226px;top:150px">“</span>
  <p class="abs ceo-quote">Aliquam tellus neque, tincidunt sit amet porta at, consequat at enim. Ut et purus nisi. Nullam tincidunt lorem sit amet nibh suscipit, eget feugiat nisl luctus. Maecenas interdum dignissim lorem quis auctor. Donec sit amet nibh eu risus luctus scelerisque. Pellentesque quis enim at mi vehicula placerat. Quisque tincidunt mauris vitae eros elementum, in fermentum odio porttitor. Sed at lorem eget erat imperdiet dapibus ac eu nisl. Maecenas interdum dignissim lorem quis auctor, fusce commodo ligula at nisl dapibus ornare.</p>
  <span class="qmark" style="left:950px;top:250px">”</span>
</section>

<!-- Team -->
<section class="section team">
  <h2 class="title" style="top:60px">Our <em>Team</em></h2>
  <svg class="abs arrows" width="104" height="40" viewBox="0 0 104 40" fill="none" stroke="var(--teal)" stroke-width="2">
    <circle cx="20" cy="20" r="18"/><path d="M23 13l-7 7 7 7"/>
    <circle cx="68" cy="20" r="18"/><path d="M65 13l7 7-7 7"/>
  </svg>
  <div class="member" style="left:262px"><div class="portrait p1" role="img" aria-label="Portrait photo of a team member"></div><h4>MARA ELLISON</h4><p>CEO / Managing Lead</p>
    <svg class="dots" width="62" height="28" viewBox="0 0 62 28" fill="none" stroke="#999" stroke-width="1"><circle cx="14" cy="14" r="13"/><rect x="8" y="10" width="12" height="8"/><path d="M8 10l6 5 6-5"/><circle cx="48" cy="14" r="13"/><path d="M44 14h8M48 10v8"/></svg></div>
  <div class="member" style="left:495px"><div class="portrait p2" role="img" aria-label="Portrait photo of a team member"></div><h4>MARA ELLISON</h4><p>CEO / Managing Lead</p>
    <svg class="dots" width="62" height="28" viewBox="0 0 62 28" fill="none" stroke="#999" stroke-width="1"><circle cx="14" cy="14" r="13"/><rect x="8" y="10" width="12" height="8"/><path d="M8 10l6 5 6-5"/><circle cx="48" cy="14" r="13"/><path d="M44 14h8M48 10v8"/></svg></div>
  <div class="member" style="left:742px"><div class="portrait p3" role="img" aria-label="Portrait photo of a team member"></div><h4>MARA ELLISON</h4><p>CEO / Managing Lead</p>
    <svg class="dots" width="62" height="28" viewBox="0 0 62 28" fill="none" stroke="#999" stroke-width="1"><circle cx="14" cy="14" r="13"/><rect x="8" y="10" width="12" height="8"/><path d="M8 10l6 5 6-5"/><circle cx="48" cy="14" r="13"/><path d="M44 14h8M48 10v8"/></svg></div>
</section>

<!-- Skills -->
<section class="section skills">
  <h2 class="title" style="top:36px">Our <em>skills</em></h2>
  <div class="skill" style="left:313px;top:212px"><div class="lab"><b>WEB DESIGN</b><span>90%</span></div><div class="bar"><i style="width:86%"></i></div></div>
  <div class="skill" style="left:626px;top:212px"><div class="lab"><b>GRAPHIC DESIGN</b><span>70%</span></div><div class="bar"><i style="width:72%"></i></div></div>
  <div class="skill" style="left:313px;top:290px"><div class="lab"><b>HTML /CSS</b><span>75%</span></div><div class="bar"><i style="width:73%"></i></div></div>
  <div class="skill" style="left:626px;top:290px"><div class="lab"><b>UI / UX</b><span>80%</span></div><div class="bar"><i style="width:84%"></i></div></div>
</section>

<!-- Services banner -->
<section class="section services photo-band" role="img" aria-label="Blurred teal-toned photo of a shoreline">
  <svg class="abs" style="left:548px;top:94px" width="104" height="116" viewBox="0 0 104 116" fill="none" stroke="#fff" stroke-width="2">
    <polygon points="52,3 100,30 100,86 52,113 4,86 4,30"/>
    <circle cx="52" cy="56" r="16"/><path d="M40 67l-4 10 10-5"/>
  </svg>
  <p class="abs services-text">Our services will lorem and ipsum<br>your aliquam</p>
</section>

<!-- Stats & testimonial -->
<section class="section stats">
  <div class="stat" style="left:275px"><b>365</b><span>Lorem ipsum</span></div>
  <div class="stat-rule" style="left:440px"></div>
  <div class="stat" style="left:449px"><b>98%</b><span>Lorem ipsum</span></div>
  <div class="stat-rule" style="left:604px"></div>
  <div class="stat" style="left:598px"><b>69</b><span>Lorem ipsum</span></div>
  <div class="stat-rule" style="left:760px"></div>
  <div class="stat" style="left:762px"><b>1,642</b><span>Lorem ipsum</span></div>
  <div class="abs avatar" role="img" aria-label="Small portrait photo of the client"></div>
  <p class="abs quote">“Fusce dapibus, tellus ac cursus commodo, tortor mauris condimentum. Duis mollis, est non commodo luctus, nisi erat.”</p>
  <p class="abs cite">DANA WHITFIELD, BRIGHTLANE</p>
  <div class="abs pager"><i></i><i></i><i class="on"></i><i></i><i></i></div>
</section>

<!-- Portfolio -->
<section class="section portfolio">
  <h2 class="title" style="top:52px">Our <em>portfolio</em></h2>
  <div class="abs filters"><span class="on">ALL</span><span>WEB</span><span>APPS</span><span>ICONS</span></div>
  <div class="work" style="left:264px;top:191px"><div class="shot" role="img" aria-label="Speaker and laptop on a desk" style="background:radial-gradient(circle 60px at 70px 90px,#2a2a2a,#6b6864 60%,transparent 80%),linear-gradient(180deg,#f1efeb 0%,#d6d0c6 60%,#8c6c4e 100%)"></div><h5>Neque Porro Quisquam</h5><p>Web, Icons, UI</p></div>
  <div class="work" style="left:494px;top:191px"><div class="shot" role="img" aria-label="Red bicycle against a white wall" style="background:radial-gradient(ellipse 80px 30px at 110px 150px,rgba(170,40,40,.7),transparent 75%),linear-gradient(90deg,#3e4a5a 0%,#5d6876 30%,#e4e0da 32%,#f0eeea 100%)"></div><h5>Neque Porro Quisquam</h5><p>Web, Icons, UI</p></div>
  <div class="work" style="left:723px;top:191px"><div class="shot" role="img" aria-label="Hands sketching on a wooden desk" style="background:radial-gradient(ellipse 70px 50px at 120px 100px,#f2efe8,transparent 75%),linear-gradient(135deg,#b2673a,#d69a68 50%,#e9d4bd)"></div><h5>Neque Porro Quisquam</h5><p>Web, Icons, UI</p></div>
  <div class="work" style="left:264px;top:469px"><div class="shot" role="img" aria-label="Kraft paper gift tags on a grey board" style="background:radial-gradient(ellipse 40px 60px at 60px 130px,#8a5a34,transparent 80%),radial-gradient(ellipse 40px 60px at 160px 130px,#9a6a40,transparent 80%),linear-gradient(135deg,#d2cfca,#b4b0aa)"></div><h5>Neque Porro Quisquam</h5><p>Web, Icons, UI</p></div>
  <div class="work" style="left:494px;top:469px"><div class="shot" role="img" aria-label="Boat wake on a bright sea" style="background:radial-gradient(ellipse 30px 90px at 108px 200px,rgba(255,255,255,.6),transparent 80%),linear-gradient(180deg,#e6d39a 0%,#c9b27a 25%,#5a8f95 45%,#2f5f6a 100%)"></div><h5>Neque Porro Quisquam</h5><p>Web, Icons, UI</p></div>
  <div class="work" style="left:723px;top:469px"><div class="shot" role="img" aria-label="City skyline across the water" style="background:linear-gradient(180deg,#a9b0b6 0%,#9aa2a9 40%,#4d545b 45%,#6a7178 62%,#7e868c 100%)"></div><h5>Neque Porro Quisquam</h5><p>Web, Icons, UI</p></div>
  <div class="btn" style="left:529px;top:764px;width:142px;height:46px">Watch more</div>
</section>

<!-- Contact -->
<section class="section contact" role="img" aria-label="Sky photo with a hot air balloon and a person with a laptop on a wooden pier">
  <div class="abs panel">
    <h2 class="title" style="width:870px;top:62px;font-size:28px">Get <em>in touch</em></h2>
    <div class="field" style="top:174px">Your Name</div>
    <div class="field" style="top:244px">Your Email</div>
    <div class="field" style="top:313px;height:157px">Your Message</div>
    <div class="btn" style="left:52px;top:494px;width:138px;height:42px">Send email</div>
    <p class="abs contact-info" style="top:167px">Lorem ipsum dolor sit amet, consectetur adipiscing elit. Donec gravida nibh. Quisque volutpat mattis eros. Nullam malesuada erat ut turpis. Suspendisse urna nibh, viverra non, semper suscipit, posuere a, pede.</p>
    <p class="abs contact-info" style="top:275px"><b>2480 Harbor Line Ave, Suite 300, Denver, CO 80202, United States</b></p>
    <p class="abs contact-info" style="top:338px"><b>T: (303) 555-0148<br>M: (303) 555-0172</b></p>
    <svg class="abs social" width="140" height="40" viewBox="0 0 140 40" fill="none" stroke="#555" stroke-width="1.4">
      <circle cx="20" cy="20" r="18"/><rect x="12" y="14" width="16" height="12"/><path d="M12 14l8 7 8-7"/>
      <circle cx="70" cy="20" r="18"/><path d="M64 12c-2 0-3 2-2 5 2 5 6 9 11 11 3 1 5 0 5-2l-3-3-3 2c-2-1-4-3-5-5l2-3z"/>
      <circle cx="120" cy="20" r="18"/><path d="M120 30c-5-6-7-9-7-12a7 7 0 0 1 14 0c0 3-2 6-7 12z"/><circle cx="120" cy="18" r="2.5"/>
    </svg>
  </div>
  <footer class="abs footer">
    <span class="abs" style="left:108px;top:32px">Copyright © 2014 corvalo.example - All Rights Reserved</span>
    <div class="abs" style="left:0;width:1200px;top:12px;text-align:center;font-size:24px;font-weight:500;line-height:24px">Corvalo<br><span style="font-size:13px">Integration Solutions</span></div>
  </footer>
</section>

</body>
</html>
```